Brightway Haus Inc. Business Card Design

Brightway Haus Inc. is in search of a great clean design for our business cards!

Looking to incorporate our full logo and watermark on side one (however, I am open to having the text and watermark separated within the design.)

On side two, I am looking to have contact information (Name, Position, Phone #, Email, Website (www.thebrightwayhaus.ca). Can have the logo and/or watermark as part of the design if applicable.

Please add tagline "Where Shine Counts" on either side 1 or 2. This tagline can be in a sans serif, serif or cursive font as long as it compliments overall design. Capitalization can be title or sentence case depending on how it fits within the design.

Get creative!! Looking for a clean, crisp, premium design! Looking for a glossy card finish with spot UV features when printed. Cards will also be printed with rounded corners. Standard dimensions (3.5 x 2).

Target Market(s)

B2B - primary clients are business owners or property management corporations. (residential jobs are few and far between)

Industry/Entity Type

Business

Contact Information for Business Card

- clean, crisp design
- double sided
- spot UV accents and glossy finish upon printing
- standard business card size (3.5 x 2) with rounded corners
- please see project description for requirements per side

Font styles to use
Sans Serif

Requirements
Must have
• - adequate bleeds with print ready files
• - cohesive design elements between side 1 & 2
• - spot UV elements (can be on both sides or just one, use your discretion)
• - colour pallet should match the logo file provided
• - incorporate tagline "where shine counts" (this tagline can be in a serif or sans serif font as long as it is complimentary to the overall design.
Nice to have
• - Premium elements with a clean design
Should not have
• - Please omit cartoon or whimsical like designs, think premium.
• - Colours should not stray from the pallet of the provided logo.

```html
<!DOCTYPE html>
<html lang="en">
<head>
<meta charset="utf-8">
<title>Brightway Haus Inc. Business Card</title>
<link rel="stylesheet" href="https://fonts.googleapis.com/css2?family=Roboto:wght@400;500;700&display=swap">
<style>
  :root {
    --teal: #0f9fa4;
    --teal-deep: #0a8d93;
    --navy: #1d1e4a;
    --ink: #222433;
    --card-light: #f4f4f4;
    --card-light-2: #e6e6e6;
    --backdrop: #e8e8e8;
  }
  * { margin: 0; padding: 0; box-sizing: border-box; }
  html, body {
    width: 1200px; height: 576px; overflow: hidden;
    background: var(--backdrop);
    font-family: "Roboto", Arial, sans-serif;
  }
  .canvas { position: relative; width: 1200px; height: 576px; }

  .card {
    position: absolute; top: 138px;
    width: 484px; height: 294px;
    border-radius: 13px; overflow: hidden;
  }
  .card--front {
    left: 82px;
    background: linear-gradient(160deg, var(--teal) 0%, var(--teal-deep) 100%);
    display: flex; align-items: center; justify-content: center; gap: 12px;
  }
  .front-mark {
    width: 26px; height: 26px; background: var(--navy);
  }
  .front-name {
    color: #ffffff; font-weight: 700; font-size: 29px; letter-spacing: -0.3px;
  }

  .card--back {
    left: 602px; width: 481px;
    background: linear-gradient(165deg, var(--card-light) 0%, #ececec 60%, var(--card-light-2) 100%);
    color: var(--ink);
  }
  .edge-tab {
    position: absolute; left: -20px; top: 34px;
    width: 30px; height: 60px; border-radius: 50%;
    background: var(--teal);
  }
  .person { position: absolute; left: 25px; top: 46px; }
  .person-name { font-size: 21px; font-weight: 500; color: var(--teal); }
  .person-role { font-size: 12px; color: var(--ink); margin-top: 4px; }

  .address {
    position: absolute; left: 25px; top: 176px;
    font-size: 13px; line-height: 18px;
  }
  .contacts {
    position: absolute; left: 25px; top: 216px;
    list-style: none; font-size: 13px;
  }
  .contacts li { display: flex; align-items: center; gap: 10px; height: 18.5px; }
  .contacts svg { width: 11px; height: 11px; fill: var(--teal); flex: none; }
  .accent { color: var(--teal); }

  .brand-block {
    position: absolute; right: 27px; top: 224px; text-align: right;
  }
  .brand-name { font-size: 22px; font-weight: 700; color: var(--teal); letter-spacing: -0.3px; }
  .tagline {
    font-size: 10px; letter-spacing: 2.6px; color: var(--navy); margin-top: 3px;
  }
</style>
</head>
<body>
<main class="canvas">
  <section class="card card--front" aria-label="Card front">
    <span class="front-mark"></span>
    <span class="front-name">BRIGHTWAY HAUS INC.</span>
  </section>

  <section class="card card--back" aria-label="Card back">
    <span class="edge-tab"></span>
    <div class="person">
      <p class="person-name">Maren Holt</p>
      <p class="person-role">Managing Director</p>
    </div>
    <p class="address">48, Alder Park Road,<br>Ontario 204</p>
    <ul class="contacts">
      <li>
        <svg viewBox="0 0 24 24" aria-hidden="true"><path d="M6.6 10.8a15.1 15.1 0 0 0 6.6 6.6l2.2-2.2c.3-.3.7-.4 1-.2 1.1.4 2.3.6 3.6.6.6 0 1 .4 1 1V20c0 .6-.4 1-1 1A17 17 0 0 1 3 4c0-.6.4-1 1-1h3.5c.6 0 1 .4 1 1 0 1.3.2 2.5.6 3.6.1.3 0 .7-.2 1z"/></svg>
        1800-555-0147
      </li>
      <li>
        <svg viewBox="0 0 24 24" aria-hidden="true"><path d="M2 5h20v14H2zm2 2v.5l8 5 8-5V7zm0 2.8V17h16V9.8l-8 5z"/></svg>
        mholt@brightwayhaus.ca
      </li>
      <li>
        <svg viewBox="0 0 24 24" aria-hidden="true"><path d="M12 2a10 10 0 1 0 0 20 10 10 0 0 0 0-20zm6.9 6h-3a15 15 0 0 0-1.3-3.9A8 8 0 0 1 18.9 8zM12 4c.8 1.2 1.5 2.5 1.9 4h-3.8c.4-1.5 1.1-2.8 1.9-4zM4.3 14a8 8 0 0 1 0-4h3.4a16 16 0 0 0 0 4zm.8 2h3a15 15 0 0 0 1.3 3.9A8 8 0 0 1 5.1 16zm3-8h-3a8 8 0 0 1 4.3-3.9C8.8 5.3 8.4 6.6 8.1 8zM12 20c-.8-1.2-1.5-2.5-1.9-4h3.8c-.4 1.5-1.1 2.8-1.9 4zm2.3-6H9.7a14 14 0 0 1 0-4h4.6a14 14 0 0 1 0 4zm.3 5.9c.6-1.2 1-2.5 1.3-3.9h3a8 8 0 0 1-4.3 3.9zm1.7-5.9a16 16 0 0 0 0-4h3.4a8 8 0 0 1 0 4z"/></svg>
        <span>www.<span class="accent">thebrightwayhaus</span>.ca</span>
      </li>
    </ul>
    <div class="brand-block">
      <p class="brand-name">BRIGHTWAY HAUS INC.</p>
      <p class="tagline">Where Shine Counts</p>
    </div>
  </section>
</main>
</body>
</html>
```